No Credit Score OD and RLC

I'm looking for a banner to display on emails as well as chatterly. The chatterly banner would need to be square and the other size is 728 x 90. We are a mortgage company that does mostly Military home loans. We would like to start out with just this banner, then do about 20 others once we find the right designer. I need something simple but that stands out. Our company website is www.oakmerelending.com. The text for this will be ( Ask about our "No Credit Score" program for RLC and OD)

```html
<!DOCTYPE html>
<html lang="en">
<head>
<meta charset="utf-8">
<title>Oakmere Lending – No Credit Score Program Banner</title>
<link href="https://fonts.googleapis.com/css2?family=Josefin+Sans:wght@300;400;600&display=swap" rel="stylesheet">
<style>
  :root {
    --paper: #ffffff;
    --ink: #1f1f1f;
    --brand-green: #5cab33;
    --brand-green-deep: #4e9a2a;
    --photo-sky: #d6e7f3;
    --photo-facade: #e9ecee;
    --photo-stone: #a59a92;
    --photo-shirt: #3f6fa8;
    --photo-shade: #6c7a86;
    --photo-foliage: #6d8f4c;
    --text-light: #ffffff;
  }
  * { margin: 0; padding: 0; box-sizing: border-box; }
  html, body {
    width: 1200px;
    height: 148px;
    overflow: hidden;
    background: var(--paper);
  }
  .banner {
    position: relative;
    width: 1200px;
    height: 148px;
    background: var(--paper);
    font-family: "Josefin Sans", sans-serif;
    overflow: hidden;
  }
  .brand {
    position: absolute;
    left: 26px;
    top: 50px;
    display: flex;
    align-items: center;
    gap: 16px;
  }
  .brand-mark {
    width: 42px;
    height: 42px;
    background: var(--ink);
  }
  .brand-name {
    color: var(--ink);
    font-weight: 600;
    line-height: 1;
  }
  .brand-name .primary {
    display: block;
    font-size: 40px;
    letter-spacing: 6px;
  }
  .brand-name .secondary {
    display: block;
    margin-top: 6px;
    font-size: 13px;
    letter-spacing: 7px;
    text-align: center;
  }
  .hero-photo {
    position: absolute;
    left: 445px;
    top: 0;
    width: 470px;
    height: 148px;
    background:
      radial-gradient(ellipse 90px 70px at 150px 95px, rgba(63,111,168,0.9), rgba(63,111,168,0) 100%),
      linear-gradient(90deg, var(--photo-foliage) 0%, rgba(109,143,76,0) 18%),
      linear-gradient(90deg, rgba(0,0,0,0) 40%, var(--photo-stone) 52%, var(--photo-facade) 70%, var(--photo-shade) 100%),
      linear-gradient(180deg, var(--photo-sky) 0%, var(--photo-facade) 40%, var(--photo-shade) 100%);
    background-blend-mode: normal, normal, multiply, normal;
  }
  .offer-panel {
    position: absolute;
    top: 0;
    right: 0;
    width: 345px;
    height: 148px;
    background: linear-gradient(90deg, var(--brand-green-deep), var(--brand-green));
    clip-path: polygon(42px 0, 100% 0, 100% 100%, 0 100%);
    display: flex;
    align-items: center;
    justify-content: center;
    padding: 10px 0 0 30px;
  }
  .offer-text {
    color: var(--text-light);
    font-weight: 300;
    font-size: 20px;
    line-height: 1.3;
    letter-spacing: 0.6px;
    text-transform: uppercase;
    text-align: center;
  }
</style>
</head>
<body>
  <div class="banner">
    <div class="brand">
      <span class="brand-mark"></span>
      <div class="brand-name">
        <span class="primary">OAKMERE</span>
        <span class="secondary">LENDING, LLC</span>
      </div>
    </div>

    <div class="hero-photo" role="img" aria-label="Couple embracing in front of a modern two-storey home with trees"></div>

    <div class="offer-panel">
      <p class="offer-text">Ask about our<br>"No Credit Score"<br>program for RLC and OD</p>
    </div>
  </div>
</body>
</html>
```